Quote Cards With KB May 2025 for Instagram

I would like to put these quotes over one of the pictures attached; Instagram (new size: 4:5 (1080 x 1350 pixels) One Quote per picture, and I want the quote to be bold or easy to read as well. I provided a few reference graphics that I really like as examples below. In very small letters at the bottom add @KBHarlowOnline

All of the pictures are attached; you can pick any photo and add one quote to it; but no stock photography

```html
<!DOCTYPE html>
<html lang="en">
<head>
<meta charset="utf-8">
<title>KB Quote Card – 90-Day Plan</title>
<link href="https://fonts.googleapis.com/css2?family=Alike&family=Montserrat:wght@600&display=swap" rel="stylesheet">
<style>
  :root {
    --pink: #ff3aa0;
    --room-wall: #4a3a3c;
    --room-floor: #b59a86;
    --window-night: #2b2f7a;
    --window-glow: #5a4fa8;
    --window-frame: #2a2226;
    --figure-dark: #1f1519;
    --figure-warm: #6a4638;
    --white: #ffffff;
  }
  html, body {
    margin: 0;
    padding: 0;
    overflow: hidden;
    background: var(--white);
  }
  .quote-card {
    position: relative;
    width: 960px;
    height: 1200px;
    overflow: hidden;
    background: var(--room-wall);
  }
  .photo {
    position: absolute;
    inset: 0;
  }
  .photo-wall {
    position: absolute;
    left: 0; top: 0;
    width: 960px; height: 1200px;
    background: linear-gradient(180deg, #5a4848 0%, var(--room-wall) 60%, #3a2e30 100%);
  }
  .photo-window {
    position: absolute;
    left: 0; top: 60px;
    width: 960px; height: 990px;
    background:
      radial-gradient(ellipse 40% 25% at 20% 85%, #3b5fc8 0%, transparent 70%),
      linear-gradient(180deg, #3a2f55 0%, var(--window-glow) 45%, var(--window-night) 100%);
  }
  .photo-window-frame {
    position: absolute;
    left: 372px; top: 0;
    width: 18px; height: 1060px;
    background: var(--window-frame);
  }
  .photo-floor {
    position: absolute;
    left: 0; top: 1040px;
    width: 960px; height: 160px;
    background: linear-gradient(180deg, #8a7468 0%, var(--room-floor) 100%);
  }
  .photo-figure {
    position: absolute;
    left: 70px; top: 70px;
    width: 400px; height: 1150px;
    border-radius: 200px 200px 60px 60px;
    background:
      radial-gradient(ellipse 28% 12% at 50% 10%, var(--figure-warm) 0%, transparent 100%),
      linear-gradient(180deg, #3a2a2a 0%, var(--figure-dark) 30%, var(--figure-dark) 100%);
    filter: blur(6px);
  }
  .pink-wash {
    position: absolute;
    inset: 0;
    background: linear-gradient(90deg,
      rgba(255, 58, 160, 0) 0%,
      rgba(255, 58, 160, 0.12) 30%,
      rgba(255, 58, 160, 0.5) 46%,
      rgba(255, 58, 160, 0.88) 62%,
      var(--pink) 78%);
  }
  .pink-wash-bottom {
    position: absolute;
    inset: 0;
    background: linear-gradient(0deg, rgba(255, 58, 160, 0.4) 0%, rgba(255, 58, 160, 0) 28%);
  }
  .frame {
    position: absolute;
    inset: 0;
  }
  .quote {
    position: absolute;
    left: 422px;
    width: 482px;
    top: 280px;
    margin: 0;
    text-align: center;
    color: var(--white);
    font-family: "Alike", Georgia, serif;
    font-weight: 400;
    font-size: 63px;
    line-height: 75.5px;
    letter-spacing: -0.3px;
    -webkit-text-stroke: 0.6px var(--white);
  }
  .quote-tagline {
    display: block;
    margin-top: 75px;
  }
  .handle {
    position: absolute;
    left: 0;
    width: 960px;
    top: 1122px;
    text-align: center;
    color: var(--white);
    font-family: "Montserrat", Arial, sans-serif;
    font-weight: 600;
    font-size: 32px;
    line-height: 40px;
  }
</style>
</head>
<body>
  <main class="quote-card">
    <div class="photo" role="img" aria-label="Photo of KB smiling in a sheer black top and black jeans, standing by a high-rise window with a city skyline at night">
      <div class="photo-wall"></div>
      <div class="photo-window"></div>
      <div class="photo-window-frame"></div>
      <div class="photo-floor"></div>
      <div class="photo-figure"></div>
    </div>
    <div class="pink-wash"></div>
    <div class="pink-wash-bottom"></div>

    <svg class="frame" width="960" height="1200" viewBox="0 0 960 1200" aria-hidden="true">
      <path d="M281 1144 H68 A36 36 0 0 1 32 1108 V75 A36 36 0 0 1 68 39 H892 A36 36 0 0 1 928 75 V1108 A36 36 0 0 1 892 1144 H673"
            fill="none" stroke="var(--white)" stroke-width="3"/>
    </svg>

    <p class="quote">
      This 90-day<br>plan helped<br>women over<br>40 slim down,<br>get a tiny waist<br>and feel<br>sexy again.
      <span class="quote-tagline">You’re next.</span>
    </p>

    <div class="handle">@KBHarlowOnline</div>
  </main>
</body>
</html>
```